SkyvornQ Business Cards and Stationary Design

Need a design for our business cards and stationary. I want to carry on the theme of the logo. I want the business cards to have a design on the back. I would like the business cards and the stationary to carry the same theme, design scheme, and branding

Target Market(s)

Airlines and Maintenance Facilities

Industry/Entity Type

Aviation

Contact Information for Business Card

Name
Position Title
Address: 4827 Trellis Hollow Road, Fort Pierce, Florida, 34951
Office Number
Mobile Number
Email
Website

Font styles to use
Serif
Sans Serif

Colors

Designer to choose colors to be used in the design.

```html
<!DOCTYPE html>
<html lang="en">
<head>
<meta charset="utf-8">
<title>SkyvornQ Business Card</title>
<link rel="stylesheet" href="https://fonts.googleapis.com/css2?family=Open+Sans:wght@300;400;600;700&display=swap">
<style>
  :root {
    --backdrop: #d9dadc;
    --backdrop-light: #e8e9ea;
    --navy: #14284f;
    --navy-mid: #1e3c74;
    --blue: #2a6fb0;
    --sky: #2aa3dd;
    --ink: #1d1d1f;
    --white: #ffffff;
    --icon: #1f4f8f;
  }
  * { margin: 0; padding: 0; box-sizing: border-box; }
  html, body { width: 1200px; height: 1099px; overflow: hidden; }
  body {
    position: relative;
    background: radial-gradient(ellipse at 20% 15%, var(--backdrop-light), var(--backdrop) 70%);
    font-family: "Open Sans", Arial, sans-serif;
  }
  .card {
    position: absolute;
    width: 782px;
    height: 447px;
    border-radius: 50px;
    overflow: hidden;
  }
  .card-front {
    left: 350px; top: 72px;
    background: var(--white);
    border: 1.5px solid #1b1b1b;
  }
  .card-back {
    left: 103px; top: 572px;
    background: radial-gradient(ellipse 60% 75% at 50% 40%, #2b9ad6 0%, #2478b8 55%, #24508a 100%);
  }
  .accent-bar {
    position: absolute; left: 0; top: 61px;
    width: 15px; height: 49px;
    background: var(--navy);
  }
  .person { position: absolute; left: 34px; top: 54px; }
  .person-name {
    font-weight: 700; font-size: 26px; color: var(--navy);
    letter-spacing: 0.2px; line-height: 1.15;
  }
  .person-title {
    font-weight: 300; font-size: 23px; color: var(--ink);
    line-height: 1.25;
  }
  .contacts { position: absolute; left: 32px; top: 214px; list-style: none; }
  .contacts li {
    display: flex; align-items: flex-start; gap: 6px;
    font-size: 17px; color: var(--ink); line-height: 28px;
  }
  .contacts li.address { margin-top: 22px; }
  .contacts svg { width: 17px; height: 17px; margin-top: 5px; flex: none; }
  .brand-front {
    position: absolute; right: 32px; top: 30px;
    display: flex; flex-direction: column; align-items: center;
  }
  .brand-mark {
    width: 104px; height: 104px; border-radius: 50%;
    border: 9px solid var(--navy-mid);
    margin-bottom: 14px;
  }
  .brand-name {
    font-weight: 700; font-size: 37px; color: var(--navy);
    letter-spacing: 6px; line-height: 1;
  }
  .front-band { position: absolute; left: 0; top: 387px; }
  .front-web {
    position: absolute; left: 34px; top: 389px;
    font-size: 20px; color: var(--white); letter-spacing: 3.4px;
  }
  .back-mark {
    position: absolute; left: 252px; top: 44px;
    width: 278px; height: 278px; border-radius: 50%;
    border: 12px solid #1f3f7a;
    display: flex; align-items: center; justify-content: center;
  }
  .back-name {
    font-weight: 700; font-size: 29px; color: var(--white);
    letter-spacing: 4px; padding-left: 4px; line-height: 1;
  }
  .back-web {
    position: absolute; left: 0; right: 0; top: 358px;
    text-align: center; padding-left: 4.5px;
    font-size: 23px; color: var(--white); letter-spacing: 4.5px;
  }
</style>
</head>
<body>

<section class="card card-front">
  <div class="accent-bar"></div>
  <div class="person">
    <p class="person-name">DORIAN KESSLER</p>
    <p class="person-title">PRESIDENT</p>
  </div>

  <ul class="contacts">
    <li>
      <svg viewBox="0 0 20 20"><circle cx="10" cy="10" r="8.6" fill="none" stroke="var(--icon)" stroke-width="1.6"/><path d="M6.6 5.6l1.8-.3 1 2.3-1.1.9a6 6 0 0 0 3.2 3.2l.9-1.1 2.3 1-.3 1.8c-4.3.3-8.1-3.5-7.8-7.8z" fill="var(--icon)"/></svg>
      <span>012-345-6789</span>
    </li>
    <li>
      <svg viewBox="0 0 20 20"><circle cx="10" cy="10" r="8.6" fill="none" stroke="var(--icon)" stroke-width="1.6"/><rect x="7.2" y="5" width="5.6" height="10" rx="1" fill="none" stroke="var(--icon)" stroke-width="1.4"/></svg>
      <span>012-345-6789</span>
    </li>
    <li>
      <svg viewBox="0 0 20 20"><circle cx="10" cy="10" r="8.6" fill="none" stroke="var(--icon)" stroke-width="1.6"/><rect x="5.5" y="7" width="9" height="6.5" fill="var(--icon)"/><path d="M5.5 7l4.5 3.6L14.5 7" fill="none" stroke="#fff" stroke-width="1"/></svg>
      <span>info@skyvornq.com</span>
    </li>
    <li class="address">
      <svg viewBox="0 0 20 20"><circle cx="10" cy="10" r="8.6" fill="none" stroke="var(--icon)" stroke-width="1.6"/><path d="M10 15s-3.4-3.6-3.4-6a3.4 3.4 0 0 1 6.8 0c0 2.4-3.4 6-3.4 6z" fill="var(--icon)"/><circle cx="10" cy="9" r="1.2" fill="#fff"/></svg>
      <span>123, Street Name, City Name<br>Zipcode-012345</span>
    </li>
  </ul>

  <div class="brand-front">
    <div class="brand-mark"></div>
    <p class="brand-name">SKYVORNQ</p>
  </div>

  <svg class="front-band" width="782" height="62" viewBox="0 0 782 62">
    <defs>
      <linearGradient id="bandBase" x1="0" x2="1" y1="0" y2="0">
        <stop offset="0" stop-color="var(--sky)"/>
        <stop offset="0.55" stop-color="var(--blue)"/>
        <stop offset="1" stop-color="var(--navy-mid)"/>
      </linearGradient>
    </defs>
    <rect x="0" y="0" width="782" height="62" fill="url(#bandBase)"/>
    <path d="M0 0 H520 C500 0 496 32 470 32 H0 Z" fill="var(--navy)"/>
  </svg>
  <p class="front-web">www.skyvornq.com</p>
</section>

<section class="card card-back">
  <div class="back-mark">
    <p class="back-name">SKYVORNQ</p>
  </div>
  <p class="back-web">www.skyvornq.com</p>
</section>

</body>
</html>
```